Harborview Estates Business Card for Apartment Buildings

Create business cards for resident managers who run apartment buildings. The audience is the public who are searching for apartment rentals, and current residents who live at the apartment building. Key design element will be incorporating the company logo, however, the logo cannot dominate. The building name and manager name are more important than the logo. Current business card design leaves little room for copy, so we may need to reduce the size on the current card to allow for more space for copy.

Target Market(s)

Adults 18-65 years of age, who are looking for an apartment rental, plus current residents who live at our apartment buildings.

Industry/Entity Type

Property Management

Contact Information for Business Card

A major design element will be use of the company logo. Important property and manager contact information must be part of the design. The size of the logo will need to be reduced to make room for building and manager contact copy.

Font styles to use
Sans Serif

Colors
3176b5
000000
959595
ffffff

Requirements
Must have
• 1) Incorporate the company logo.
• 2) Use the company colors (dark blue, black/grey, over white).
• 3) FEATURE THE BUILDING NAME
• 4) FEATURE THE MANAGER NAME
• 5) The company name is less important than BUILDING and MANAGER
• 6) Manager contact information
• **SEE ATTACHED CREATIVE BRIEF**
Nice to have
• 1) Back of card logo watermark
• 2) Ability to write notes on back of carfd
Should not have
• Avoid letting the company logo dominate the card, the building name and manager are more important than the company logo.

```html
<!DOCTYPE html>
<html lang="en">
<head>
<meta charset="utf-8">
<title>Harborview Estates Business Card</title>
<link href="https://fonts.googleapis.com/css2?family=Work+Sans:wght@400;500;700&display=swap" rel="stylesheet">
<style>
  :root {
    --brand-blue: #1a6fb5;
    --ink: #000000;
    --grey: #959595;
    --paper: #ffffff;
    --backdrop: #e4e4e4;
  }
  * { box-sizing: border-box; margin: 0; padding: 0; }
  html, body {
    width: 1200px; height: 930px; overflow: hidden;
    background: var(--backdrop);
    font-family: "Work Sans", sans-serif;
  }
  .canvas { position: relative; width: 1200px; height: 930px; }
  .card {
    position: absolute; width: 540px; height: 309px;
    box-shadow: 0 6px 18px rgba(0,0,0,0.18);
    overflow: hidden;
  }
  /* Back of card */
  .card-back {
    left: 100px; top: 110px;
    background: var(--brand-blue);
    color: var(--paper);
  }
  .card-back .company-name {
    position: absolute; left: 0; right: 0; top: 118px;
    text-align: center; font-size: 36px; font-weight: 700;
    letter-spacing: 0.5px; color: var(--paper);
  }
  .card-back .website {
    position: absolute; right: 44px; bottom: 34px;
    font-size: 14px; font-weight: 500; letter-spacing: 0.3px;
  }
  /* Front of card */
  .card-front {
    left: 560px; top: 500px;
    background: var(--paper);
  }
  .brand-area {
    position: absolute; left: 0; top: 0; width: 44%; height: 100%;
    display: flex; align-items: center; justify-content: center;
  }
  .brand-area .company-name {
    font-size: 22px; font-weight: 700; color: var(--brand-blue);
    letter-spacing: 0.3px; text-align: center; line-height: 1.15;
  }
  .info-panel {
    position: absolute; right: 0; top: 0; width: 56%; height: 100%;
    background: var(--brand-blue); color: var(--paper);
    padding: 34px 22px 0 34px;
  }
  .info-panel::before {
    content: ""; position: absolute; left: -18px; top: 50px;
    border-top: 18px solid transparent; border-bottom: 18px solid transparent;
    border-right: 18px solid var(--brand-blue);
  }
  .manager-name { font-size: 19px; font-weight: 700; letter-spacing: 0.3px; text-transform: uppercase; }
  .manager-title { font-size: 13px; margin-top: 2px; }
  .building { margin-top: 18px; font-size: 13px; line-height: 1.35; }
  .building .building-name { font-weight: 500; }
  .contact-list { list-style: none; margin-top: 16px; font-size: 12.5px; line-height: 1.5; }
  .contact-list li { display: flex; align-items: center; gap: 9px; }
  .contact-list svg { width: 10px; height: 10px; flex: none; fill: var(--paper); }
</style>
</head>
<body>
<div class="canvas">

  <section class="card card-back" aria-label="Back of business card">
    <div class="company-name">Harborview Estates</div>
    <div class="website">www.harborviewest.com</div>
  </section>

  <section class="card card-front" aria-label="Front of business card">
    <div class="brand-area">
      <div class="company-name">Harborview Estates</div>
    </div>
    <div class="info-panel">
      <div class="manager-name">Marisol Quintero</div>
      <div class="manager-title">Resident Manager</div>
      <div class="building">
        <div class="building-name">Bayside Court Apartments</div>
        <div>2845 Lindell Avenue</div>
        <div>Coral Bay, CA 92199</div>
      </div>
      <ul class="contact-list">
        <li><svg viewBox="0 0 10 10" aria-hidden="true"><path d="M2 0.5l2 2-1 1.2c.6 1.3 1.6 2.3 2.9 2.9L7 5.5l2 2-1.3 1.7C4 9 1 6 .7 2.2z"/></svg>555-201-4410</li>
        <li><svg viewBox="0 0 10 10" aria-hidden="true"><path d="M2.5 0h5v10h-5zM3.3 1v7h3.4V1z"/></svg>555-201-4475</li>
        <li><svg viewBox="0 0 10 10" aria-hidden="true"><path d="M2 0h5v3H2zM0 3.5h10v4H8v2.5H2V7.5H0zM3 6.5h4v2.5H3z"/></svg>555-201-4490</li>
        <li><svg viewBox="0 0 10 10" aria-hidden="true"><path d="M0 2h10v6H0zM.8 2.6L5 5.6l4.2-3z" fill-rule="evenodd"/></svg>marisol@harborviewest.com</li>
        <li><svg viewBox="0 0 10 10" aria-hidden="true"><circle cx="5" cy="5" r="4.5"/></svg>www.harborviewest.com</li>
      </ul>
    </div>
  </section>

</div>
</body>
</html>
```